Silver Bloom Marisol's Cleaning Service Business Cards Project

A business card with all contact details with logo design on there (already have a logo) eye catching Logo and contact info on one side, full logo on the back, must target upper class residential and corporate companies, fitness companies, still keep it on the feminine side of things , must look elegant

Target Market(s)

Upper class homes and corporate companies

Industry/Entity Type

Cleaning Service

Contact Information for Business Card

Name: Marisol Quenby
Position: Director
ABN: 31647209853
Email: marisolssilvercleaning@tidymail.example
Number: 0417906354

Font styles to use
Decorative

Colors

Designer to choose colors to be used in the design.

Requirements
Must have
• Available Sydney Wide, contact info and logo on one side, full logo on the back
Nice to have
• Professional appearance
Should not have
• Cheap advert looking stuff

```html
<!DOCTYPE html>
<html lang="en">
<head>
<meta charset="utf-8">
<title>Silver Bloom Marisol's Cleaning Service – Business Card</title>
<link rel="stylesheet" href="https://fonts.googleapis.com/css2?family=Roboto:wght@400;500;700&display=swap">
<style>
  :root {
    --page: #e4e5e8;
    --card-white: #ffffff;
    --card-white-edge: #eeeff1;
    --ink: #1f2330;
    --ink-soft: #3a3f4d;
    --navy: #262b3b;
    --navy-deep: #1e2230;
    --silver: #d9dbe0;
    --ornament: #3a4052;
  }
  * { box-sizing: border-box; margin: 0; padding: 0; }
  html, body { width: 1200px; height: 900px; overflow: hidden; }
  body {
    background: var(--page);
    font-family: "Roboto", Arial, sans-serif;
    color: var(--ink);
    display: flex;
    flex-direction: column;
    align-items: center;
    justify-content: center;
    gap: 40px;
  }
  .card {
    width: 620px;
    height: 379px;
    border-radius: 22px;
    position: relative;
    overflow: hidden;
    box-shadow: 0 10px 28px rgba(20, 24, 36, 0.22);
  }

  /* Front */
  .card-front {
    background: radial-gradient(ellipse at 60% 40%, var(--card-white) 40%, var(--card-white-edge) 100%);
    display: flex;
    align-items: center;
  }
  .brand {
    width: 270px;
    display: flex;
    flex-direction: column;
    align-items: center;
    gap: 8px;
    text-align: center;
  }
  .brand-mark {
    width: 14px; height: 14px;
    border-radius: 50%;
    background: var(--ink);
    margin-bottom: 4px;
  }
  .brand-name {
    font-weight: 500;
    font-size: 26px;
    letter-spacing: 3px;
    text-transform: uppercase;
    color: var(--ink);
  }
  .brand-tagline {
    font-weight: 500;
    font-size: 9.5px;
    letter-spacing: 2.4px;
    text-transform: uppercase;
    color: var(--ink);
  }
  .divider {
    width: 2px;
    height: 150px;
    background: var(--ink);
  }
  .details {
    padding-left: 32px;
    font-size: 14.5px;
    line-height: 1.5;
    color: var(--ink-soft);
  }
  .person-name {
    font-weight: 700;
    font-size: 27px;
    letter-spacing: 0.5px;
    text-transform: uppercase;
    color: var(--ink);
    line-height: 1.1;
  }
  .person-role { font-size: 14px; margin-bottom: 8px; }
  .contact-line { display: flex; align-items: center; gap: 8px; }
  .contact-line svg { width: 12px; height: 12px; flex: none; }
  .contact-email { font-size: 13.5px; }

  /* Back */
  .card-back {
    background: var(--navy);
    display: flex;
    align-items: center;
    justify-content: center;
  }
  .ornament-field {
    position: absolute;
    inset: 0;
    background:
      radial-gradient(ellipse at 18% 30%, var(--ornament) 0%, transparent 45%),
      radial-gradient(ellipse at 85% 75%, var(--ornament) 0%, transparent 45%),
      linear-gradient(135deg, var(--navy) 0%, var(--navy-deep) 100%);
  }
  .back-brand {
    position: relative;
    display: flex;
    flex-direction: column;
    align-items: center;
    gap: 12px;
    text-align: center;
  }
  .back-brand .brand-mark { background: var(--silver); width: 18px; height: 18px; }
  .back-brand .brand-name { color: var(--silver); font-size: 40px; letter-spacing: 5px; }
  .back-brand .brand-tagline { color: var(--silver); font-size: 13px; letter-spacing: 3.6px; }
</style>
</head>
<body>

  <section class="card card-front" aria-label="Card front">
    <div class="brand">
      <span class="brand-mark"></span>
      <span class="brand-name">Silver Bloom</span>
      <span class="brand-tagline">Marisol's Cleaning Service</span>
    </div>
    <div class="divider"></div>
    <div class="details">
      <p class="person-name">Marisol Quenby</p>
      <p class="person-role">Director</p>
      <p>ABN: 31647209853</p>
      <p class="contact-line">
        <svg viewBox="0 0 24 24" aria-hidden="true"><path fill="#1f2330" d="M6.6 10.8a15.1 15.1 0 0 0 6.6 6.6l2.2-2.2c.3-.3.7-.4 1-.2 1.1.4 2.3.6 3.6.6.6 0 1 .4 1 1V20c0 .6-.4 1-1 1C10.6 21 3 13.4 3 4c0-.6.4-1 1-1h3.5c.6 0 1 .4 1 1 0 1.3.2 2.5.6 3.6.1.3 0 .7-.2 1z"/></svg>
        0417906354
      </p>
      <p class="contact-line contact-email">
        <svg viewBox="0 0 24 24" aria-hidden="true"><rect x="2.5" y="5" width="19" height="14" rx="1.5" fill="none" stroke="#1f2330" stroke-width="2"/><path d="M3 6l9 7 9-7" fill="none" stroke="#1f2330" stroke-width="2"/></svg>
        marisolssilvercleaning@tidymail.example
      </p>
    </div>
  </section>

  <section class="card card-back" aria-label="Card back">
    <div class="ornament-field" role="img" aria-label="Faint flourishing vine and swirl ornament pattern across the card"></div>
    <div class="back-brand">
      <span class="brand-mark"></span>
      <span class="brand-name">Silver Bloom</span>
      <span class="brand-tagline">Marisol's Cleaning Service</span>
    </div>
  </section>

</body>
</html>
```